Request for Business Card Design

Hi. My name is Marlene, I am looking for a new business card design for my company, Quarrow Signal Instruments, LLC. I really like the design you did for Tarsel Venture and was hoping you could do something similar using our full logo and our mark. I am also open to any raised texture design using our mark. I have attached our full logo, which would need to be somewhere on the card, as well as the mark in both outline and full form, as well as our brand colors / guide. The card does not have to be white, as long as our logo and mark appear. I actually like darker colored business cards more, but am open to all options. If you are interested in working with me, please let me know. We would also take the business card design into letterhead design if you can do that.

```html
<!DOCTYPE html>
<html lang="en">
<head>
<meta charset="utf-8">
<title>Quarrow Signal Instruments – Business Card</title>
<link rel="stylesheet" href="https://fonts.googleapis.com/css2?family=Saira:wght@500;700;800&family=Arimo:wght@400;700&display=swap">
<style>
  :root {
    --page: #121212;
    --card: #232323;
    --card-deep: #1d1d1d;
    --accent: #0b90b8;
    --ink: #f2f2ef;
    --ink-soft: #d9d9d6;
  }
  * { box-sizing: border-box; margin: 0; padding: 0; }
  html, body { width: 1200px; height: 963px; overflow: hidden; }
  body {
    background: var(--page);
    display: flex;
    align-items: center;
    justify-content: center;
    gap: 48px;
    font-family: "Arimo", Arial, sans-serif;
  }
  .card {
    position: relative;
    width: 540px;
    height: 309px;
    background: var(--card);
    border-radius: 22px;
    border-bottom: 4px solid var(--accent);
    overflow: hidden;
    box-shadow: 0 18px 40px rgba(0,0,0,.55);
  }

  /* Front */
  .brand {
    position: absolute;
    top: 34px;
    left: 36px;
    display: flex;
    align-items: center;
    gap: 14px;
  }
  .brand-dot {
    width: 34px; height: 34px;
    border-radius: 50%;
    background: var(--accent);
  }
  .brand-name {
    font-family: "Saira", sans-serif;
    font-weight: 800;
    font-size: 30px;
    letter-spacing: 3px;
    line-height: 1;
    color: var(--ink);
  }
  .brand-tagline {
    font-family: "Saira", sans-serif;
    font-weight: 700;
    font-size: 9.5px;
    letter-spacing: 1px;
    color: var(--ink);
    margin-top: 3px;
  }
  .person {
    position: absolute;
    top: 120px;
    left: 36px;
  }
  .person-name {
    font-family: "Saira", sans-serif;
    font-weight: 800;
    font-size: 20px;
    letter-spacing: .5px;
    color: var(--accent);
    text-transform: uppercase;
  }
  .person-title {
    font-size: 14px;
    color: var(--ink-soft);
    margin-top: 1px;
  }
  .contact {
    position: absolute;
    top: 188px;
    left: 36px;
    list-style: none;
    display: flex;
    flex-direction: column;
    gap: 8px;
  }
  .contact li {
    display: flex;
    align-items: center;
    gap: 10px;
    font-size: 14px;
    color: var(--ink-soft);
  }
  .contact svg { width: 15px; height: 15px; flex: none; }
  .address {
    position: absolute;
    right: 36px;
    bottom: 28px;
    text-align: right;
    font-size: 14px;
    line-height: 1.35;
    color: var(--ink-soft);
  }

  /* Back */
  .back-texture {
    position: absolute;
    inset: 0;
    background: radial-gradient(ellipse at 50% 45%, #282828 0%, var(--card) 55%, var(--card-deep) 100%);
  }
  .back-brand {
    position: absolute;
    inset: 0;
    display: flex;
    flex-direction: column;
    align-items: center;
    justify-content: center;
  }
  .back-name {
    font-family: "Saira", sans-serif;
    font-weight: 800;
    font-size: 62px;
    letter-spacing: 8px;
    line-height: 1;
    color: var(--ink);
  }
  .back-tagline {
    font-family: "Saira", sans-serif;
    font-weight: 700;
    font-size: 17px;
    letter-spacing: 2px;
    color: var(--ink);
    margin-top: 6px;
  }
</style>
</head>
<body>
  <section class="card card-front">
    <div class="brand">
      <span class="brand-dot"></span>
      <div>
        <div class="brand-name">QUARROW</div>
        <div class="brand-tagline">SIGNAL INSTRUMENTS</div>
      </div>
    </div>

    <div class="person">
      <div class="person-name">Marlene Hale</div>
      <div class="person-title">Manager</div>
    </div>

    <ul class="contact">
      <li>
        <svg viewBox="0 0 24 24" fill="none" stroke="var(--accent)" stroke-width="2" stroke-linecap="round" stroke-linejoin="round"><path d="M5 3h4l2 5-2.5 1.5a11 11 0 0 0 6 6L16 13l5 2v4a2 2 0 0 1-2 2A16 16 0 0 1 3 5a2 2 0 0 1 2-2z"/></svg>
        987-604-3158
      </li>
      <li>
        <svg viewBox="0 0 24 24" fill="none" stroke="var(--accent)" stroke-width="2" stroke-linejoin="round"><rect x="3" y="5" width="18" height="14" rx="1"/><path d="M3 6l9 7 9-7"/></svg>
        hello@quarrowsignal.com
      </li>
      <li>
        <svg viewBox="0 0 24 24" fill="none" stroke="var(--accent)" stroke-width="2"><circle cx="12" cy="12" r="9"/><path d="M3 12h18M12 3c3 3 3 15 0 18M12 3c-3 3-3 15 0 18"/></svg>
        www.quarrowsignal.com
      </li>
    </ul>

    <p class="address">Your Address, City<br>State, Zip 0000</p>
  </section>

  <section class="card card-back">
    <div class="back-texture" role="img" aria-label="Raised blind-embossed repeating brand mark texture across the card"></div>
    <div class="back-brand">
      <div class="back-name">QUARROW</div>
      <div class="back-tagline">SIGNAL INSTRUMENTS</div>
    </div>
  </section>
</body>
</html>
```